Veranix - Solution provider in business consulting

Veranix is a swiss based company providing solutions for developing markets. The business covers various fields of business consulting, such as supply chain, product costs, quality management and manufacturing management. The Business operates in a efficient, straight and solution oriented manner.
The final design should communicate these characteristics. Asian people as well as as western people shall identify the qualities of the company at first sight.
The customer needs business cards with a simple view but an recognizable design, printed in high quality. Engraved elements such as the globe or simple words are possible.
Available colors are: (RAL)
102/102/102
51/102/102
153/204/153
255/102/51
Font: Calibri

```html
<!DOCTYPE html>
<html lang="en">
<head>
<meta charset="utf-8">
<title>Veranix – Business Card</title>
<link href="https://fonts.googleapis.com/css2?family=Carlito:wght@400;700&display=swap" rel="stylesheet">
<style>
  :root {
    --paper: #ffffff;
    --card: #808080;
    --stripe: #c8c8c8;
    --ink: #111111;
    --brand-grey: #7a7a7a;
    --crop: #000000;
  }
  html, body {
    margin: 0;
    padding: 0;
    width: 1200px;
    height: 843px;
    overflow: hidden;
    background: var(--paper);
  }
  .sheet {
    position: relative;
    width: 1200px;
    height: 843px;
    font-family: "Carlito", Calibri, sans-serif;
    color: var(--ink);
  }
  .crop-marks {
    position: absolute;
    inset: 0;
  }
  .card {
    position: absolute;
    left: 98px;
    top: 135px;
    width: 1000px;
    height: 571px;
    background: var(--card);
    border-bottom-right-radius: 72px;
    overflow: hidden;
  }
  .brand-stripe {
    position: absolute;
    left: 156px;
    top: 0;
    width: 63px;
    height: 100%;
    background: var(--stripe);
  }
  .brand-name {
    position: absolute;
    left: 187px;
    top: 284px;
    transform: translate(-50%, -50%) rotate(-90deg);
    font-size: 76px;
    font-weight: 400;
    color: var(--brand-grey);
    letter-spacing: 1px;
    white-space: nowrap;
    line-height: 1;
  }
  .website {
    position: absolute;
    left: 278px;
    top: 284px;
    transform: translate(-50%, -50%) rotate(-90deg);
    font-size: 32px;
    white-space: nowrap;
    line-height: 1;
  }
  .details {
    position: absolute;
    right: 120px;
    top: 81px;
    text-align: right;
    font-size: 32px;
    line-height: 34px;
  }
  .person-name { font-weight: 700; margin: 0; }
  .person-role { margin: 0 0 63px; }
  .contact-list {
    list-style: none;
    margin: 0 0 52px;
    padding: 0;
  }
  .contact-item {
    display: flex;
    justify-content: flex-end;
    align-items: center;
    gap: 12px;
    height: 32px;
  }
  .contact-icon { width: 32px; height: 28px; flex: none; }
  .address { font-style: normal; margin: 0; line-height: 33px; }
</style>
</head>
<body>
<div class="sheet">
  <svg class="crop-marks" width="1200" height="843" viewBox="0 0 1200 843" aria-hidden="true">
    <g stroke="var(--crop)" stroke-width="1" fill="none">
      <line x1="85" y1="0" x2="85" y2="72"/>
      <line x1="118" y1="35" x2="118" y2="93"/>
      <line x1="0" y1="83" x2="72" y2="83"/>
      <line x1="35" y1="116" x2="93" y2="116"/>

      <line x1="1117" y1="0" x2="1117" y2="72"/>
      <line x1="1084" y1="35" x2="1084" y2="93"/>
      <line x1="1129" y1="83" x2="1200" y2="83"/>
      <line x1="1106" y1="116" x2="1165" y2="116"/>

      <line x1="85" y1="773" x2="85" y2="843"/>
      <line x1="118" y1="750" x2="118" y2="809"/>
      <line x1="0" y1="759" x2="72" y2="759"/>
      <line x1="35" y1="725" x2="93" y2="725"/>

      <line x1="1117" y1="773" x2="1117" y2="843"/>
      <line x1="1084" y1="750" x2="1084" y2="809"/>
      <line x1="1129" y1="759" x2="1200" y2="759"/>
      <line x1="1106" y1="725" x2="1165" y2="725"/>
    </g>
  </svg>

  <div class="card">
    <div class="brand-stripe"></div>
    <div class="brand-name">veranix</div>
    <div class="website">www.veranix.ch</div>

    <div class="details">
      <p class="person-name">Marco Hegner</p>
      <p class="person-role">CEO</p>

      <ul class="contact-list">
        <li class="contact-item">
          <svg class="contact-icon" viewBox="0 0 30 26" aria-label="Mobile">
            <rect x="8" y="2" width="12" height="21" rx="2" transform="rotate(-25 14 13)" fill="none" stroke="var(--ink)" stroke-width="2"/>
            <circle cx="18" cy="20" r="1.5" fill="var(--ink)"/>
          </svg>
          <span>+41 79 555 0184</span>
        </li>
        <li class="contact-item">
          <svg class="contact-icon" viewBox="0 0 30 26" aria-label="Phone">
            <path d="M10 2 L14 7 L11 10 C12 14 15 17 19 19 L22 16 L27 20 L24 24 C14 24 6 15 6 5 Z" fill="var(--ink)"/>
          </svg>
          <span>+41 71 555 0237</span>
        </li>
        <li class="contact-item">
          <svg class="contact-icon" viewBox="0 0 34 26" aria-label="Email">
            <path d="M2 11 L17 2 L32 11 L32 24 L2 24 Z M2 11 L17 18 L32 11 M2 24 L13 16 M32 24 L21 16" fill="none" stroke="var(--ink)" stroke-width="2" stroke-linejoin="round"/>
          </svg>
          <span>marco.hegner@veranix.ch</span>
        </li>
      </ul>

      <address class="address">
        Veranix GmbH<br>
        Feldweg 14<br>
        9240 Uzwil<br>
        Switzerland
      </address>
    </div>
  </div>
</div>
</body>
</html>
```